Need help in designing new business card utilizing our new logo.

BuildMark Solutions works with Construction Business Owners, Managers & IT Professionals to strengthen software usage and increase user productivity.

Our Construction Accounting and Mobile Field Management Software Clients engage with us in the following areas:

New Software Implementations
Software Re-Implementations
Redesigning Software Usage at the User Level
Project Coordination & Management
Continued Software Support

Old tag line:
Weighing Options - Implementing Solutions

www.buildmark-solutions.example

Ridge 4 is a product, but not needed for a new business card.

```html
<!DOCTYPE html>
<html lang="en">
<head>
<meta charset="utf-8">
<title>BuildMark Solutions – Business Card</title>
<link href="https://fonts.googleapis.com/css2?family=Montserrat:wght@400;500;600;700&display=swap" rel="stylesheet">
<style>
  :root {
    --brand-blue: #2b34a6;
    --brand-blue-deep: #232b94;
    --accent-grey: #c4c6cc;
    --paper: #ffffff;
    --ink-grey: #555a66;
    --backdrop: #4a4540;
  }
  * { box-sizing: border-box; margin: 0; padding: 0; }
  html, body {
    width: 1200px; height: 930px; overflow: hidden;
    background: var(--backdrop);
    font-family: "Montserrat", sans-serif;
  }
  .canvas { position: relative; width: 1200px; height: 930px; }

  .card {
    position: absolute;
    width: 640px; height: 366px;
    border-radius: 16px;
    overflow: hidden;
    box-shadow: 0 10px 24px rgba(0,0,0,.35);
  }

  /* ---------- Front ---------- */
  .card--front {
    left: 70px; top: 60px;
    background: var(--brand-blue);
    color: var(--paper);
    display: flex; flex-direction: column; align-items: center; justify-content: center;
  }
  .brand { display: flex; align-items: center; gap: 18px; }
  .brand__square { flex: none; width: 58px; height: 58px; background: currentColor; }
  .brand__rule { flex: none; width: 1.5px; height: 78px; background: currentColor; }
  .brand__name { font-weight: 600; line-height: 1; white-space: nowrap; }
  .brand__name .line1 { display: block; font-size: 40px; letter-spacing: .5px; }
  .brand__name .line2 { display: block; font-size: 15px; letter-spacing: 10px; margin-top: 6px; }
  .services {
    margin-top: 38px; list-style: none; text-align: center;
    font-size: 15px; font-weight: 400; line-height: 1.5;
  }

  /* ---------- Back ---------- */
  .card--back {
    left: 490px; top: 500px;
    background: var(--paper);
  }
  .card--back .wave { position: absolute; left: 0; bottom: 0; width: 640px; height: 366px; }
  .back__brand {
    position: absolute; left: 36px; top: 118px;
    width: 262px;
    color: var(--brand-blue);
  }
  .back__brand .brand { gap: 12px; }
  .back__brand .brand__square { width: 40px; height: 40px; }
  .back__brand .brand__rule { height: 56px; }
  .back__brand .brand__name .line1 { font-size: 25px; letter-spacing: .3px; }
  .back__brand .brand__name .line2 { font-size: 10px; letter-spacing: 7px; margin-top: 5px; color: var(--accent-grey); }
  .tagline {
    margin-top: 16px;
    font-size: 14px; font-weight: 600; line-height: 1.35;
  }
  .divider {
    position: absolute; left: 318px; top: 38px;
    width: 1.5px; height: 180px; background: var(--brand-blue);
  }
  .contact { position: absolute; left: 338px; top: 34px; color: var(--ink-grey); }
  .contact__name { font-size: 22px; font-weight: 700; color: var(--brand-blue-deep); }
  .contact__role { font-size: 12.5px; margin: 2px 0 10px 18px; }
  .contact__list { list-style: none; font-size: 12.5px; line-height: 1.6; margin-left: 18px; }
  .contact__list li { display: flex; align-items: center; gap: 8px; white-space: nowrap; }
  .contact__list svg { flex: none; width: 11px; height: 11px; fill: none; stroke: var(--brand-blue); stroke-width: 1.6; }
  .contact__address { font-size: 12.5px; line-height: 1.5; margin: 8px 0 0 36px; }
</style>
</head>
<body>
<main class="canvas">

  <section class="card card--front" aria-label="Business card front">
    <div class="brand">
      <span class="brand__square" aria-hidden="true"></span>
      <span class="brand__rule" aria-hidden="true"></span>
      <span class="brand__name"><span class="line1">BUILDMARK</span><span class="line2">SOLUTIONS</span></span>
    </div>
    <ul class="services">
      <li>New Software Implementations | Software Re-Implementations</li>
      <li>Redesigning Software Usage at the User Level</li>
      <li>Project Coordination &amp; Management</li>
      <li>Continued Software Support</li>
    </ul>
  </section>

  <section class="card card--back" aria-label="Business card back">
    <svg class="wave" viewBox="0 0 640 366" preserveAspectRatio="none" aria-hidden="true">
      <path d="M0 310 C 200 262, 430 268, 640 232 L640 366 L0 366 Z" fill="var(--accent-grey)"/>
      <path d="M0 326 C 200 280, 440 286, 640 250 L640 366 L0 366 Z" fill="var(--brand-blue)"/>
    </svg>

    <div class="back__brand">
      <div class="brand">
        <span class="brand__square" aria-hidden="true"></span>
        <span class="brand__rule" aria-hidden="true"></span>
        <span class="brand__name"><span class="line1">BUILDMARK</span><span class="line2">SOLUTIONS</span></span>
      </div>
      <p class="tagline">Construction Accounting<br>Software Consultants</p>
    </div>

    <span class="divider" aria-hidden="true"></span>

    <div class="contact">
      <p class="contact__name">Dana R. Whitfield</p>
      <p class="contact__role">Owner</p>
      <ul class="contact__list">
        <li><svg viewBox="0 0 12 12"><path d="M2 1.5 L4.5 1.5 L5 4 L3.6 5 C4.3 6.6 5.4 7.7 7 8.4 L8 7 L10.5 7.5 L10.5 10 C5.5 10 2 6.5 2 1.5 Z"/></svg>800-555-0142 ext.100</li>
        <li><svg viewBox="0 0 12 12"><rect x="3" y="1" width="6" height="10" rx="1"/><path d="M5 9 H7"/></svg>555-014-2298</li>
        <li><svg viewBox="0 0 12 12"><rect x="1" y="2.5" width="10" height="7"/><path d="M1 2.5 L6 6.5 L11 2.5"/></svg>dana.w@buildmark-solutions.example</li>
        <li><svg viewBox="0 0 12 12"><circle cx="6" cy="6" r="4.8"/><path d="M1.2 6 H10.8 M6 1.2 C3.5 4 3.5 8 6 10.8 M6 1.2 C8.5 4 8.5 8 6 10.8"/></svg>www.buildmark-solutions.example</li>
      </ul>
      <p class="contact__address">48 Harbor Lane - Suite 12<br>Millbrook NY 10000</p>
    </div>
  </section>

</main>
</body>
</html>
```